Business Card Design

Online clothing womens clothing store, I sell my clothing online and at the markets.

i would like the attached picture on the front of the card and the contact information on the back.

Industry/Entity Type

Business

Contact Information for Business Card

Marlow Thread
Karen Whitfield
(Instagram symbol) _marlow_thread_
(Facebook symbol) www.fakebookexample.com/marlowthreadau/

W : www.marlowthread.example.au
E : info@marlowthread.example.au
P : 0498716204

```html
<!DOCTYPE html>
<html lang="en">
<head>
<meta charset="utf-8">
<title>Marlow Thread – Business Card</title>
<link rel="stylesheet" href="https://fonts.googleapis.com/css2?family=Jost:wght@300&family=Open+Sans:wght@400;700&family=Special+Elite&display=swap">
<style>
  :root {
    --page: #ecebe8;
    --card: #ffffff;
    --ink: #111111;
    --teal: #0f4a5c;
    --teal-light: #1d5d70;
    --swoosh: #0a0a0a;
    --mist-light: #dfe3e4;
    --mist-mid: #9fb0b4;
    --mist-dark: #4a4e63;
    --front-type: #ffffff;
  }
  * { margin: 0; padding: 0; box-sizing: border-box; }
  html, body { width: 1200px; height: 892px; overflow: hidden; }
  body {
    background: var(--page);
    display: flex;
    flex-direction: column;
    align-items: center;
    justify-content: center;
    gap: 56px;
    font-family: "Open Sans", sans-serif;
  }
  .card {
    position: relative;
    width: 640px;
    height: 366px;
    background: var(--card);
    overflow: hidden;
    box-shadow: 0 6px 18px rgba(0,0,0,0.18);
  }
  /* Contact side */
  .card__band { position: absolute; inset: 0; width: 100%; height: 100%; }
  .brand-name {
    position: absolute;
    top: 58px;
    left: 220px;
    font-family: "Jost", sans-serif;
    font-weight: 300;
    font-size: 34px;
    letter-spacing: 9px;
    color: var(--ink);
  }
  .person-name {
    position: absolute;
    top: 138px;
    left: 40px;
    font-weight: 700;
    font-size: 26px;
    color: var(--ink);
  }
  .divider {
    position: absolute;
    left: 322px;
    top: 132px;
    width: 2px;
    height: 130px;
    background: var(--ink);
  }
  .contact-list {
    position: absolute;
    left: 342px;
    top: 160px;
    list-style: none;
    font-size: 16px;
    line-height: 24px;
    color: var(--ink);
  }
  .contact-list li { display: flex; align-items: center; gap: 8px; }
  .contact-list svg { width: 15px; height: 15px; flex: none; }
  .social {
    position: absolute;
    display: flex;
    align-items: center;
    gap: 14px;
    color: #ffffff;
    font-size: 17px;
  }
  .social--instagram { left: 40px; top: 288px; }
  .social--facebook { left: 236px; top: 322px; }
  .social__mark-circle { width: 18px; height: 18px; border-radius: 50%; background: #ffffff; }
  .social__mark-square { width: 16px; height: 16px; background: #ffffff; }
  /* Image side */
  .card--front { background: var(--mist-light); }
  .front-photo {
    position: absolute;
    inset: 0;
    background:
      radial-gradient(ellipse at 72% 55%, var(--mist-dark) 0%, #6b7184 35%, transparent 70%),
      linear-gradient(135deg, var(--mist-light) 0%, #cfd6d8 40%, var(--mist-mid) 100%);
  }
  .front-title {
    position: absolute;
    left: 40px;
    top: 150px;
    font-family: "Special Elite", monospace;
    font-size: 62px;
    line-height: 1;
    letter-spacing: 2px;
    color: var(--front-type);
    text-transform: uppercase;
  }
</style>
</head>
<body>

  <section class="card card--contact" aria-label="Contact side">
    <svg class="card__band" viewBox="0 0 640 366" preserveAspectRatio="none" aria-hidden="true">
      <defs>
        <linearGradient id="bandFill" x1="0" y1="0" x2="1" y2="0">
          <stop offset="0" stop-color="var(--teal)"/>
          <stop offset="0.6" stop-color="var(--teal)"/>
          <stop offset="1" stop-color="var(--teal-light)"/>
        </linearGradient>
      </defs>
      <path d="M0,236 C180,250 330,318 640,318 L640,330 C330,334 180,272 0,262 Z" fill="var(--swoosh)"/>
      <path d="M0,262 C180,272 330,334 640,330 L640,366 L0,366 Z" fill="url(#bandFill)"/>
    </svg>

    <div class="brand-name">MARLOW THREAD</div>
    <div class="person-name">Karen Whitfield</div>
    <div class="divider"></div>

    <ul class="contact-list">
      <li>
        <svg viewBox="0 0 16 16"><rect width="16" height="16" fill="#111"/><path d="M5 3 L7 5 L6 7 Q7 9 9 10 L11 9 L13 11 L11 13 Q6 12 3 5 Z" fill="#fff"/></svg>
        0498716204
      </li>
      <li>
        <svg viewBox="0 0 16 16"><rect width="16" height="16" fill="#111"/><rect x="3" y="5" width="10" height="7" fill="#fff"/><path d="M3 5 L8 9 L13 5" stroke="#111" fill="none"/></svg>
        info@marlowthread.example.au
      </li>
      <li>
        <svg viewBox="0 0 16 16"><rect width="16" height="16" fill="#111"/><circle cx="8" cy="8" r="5" fill="none" stroke="#fff" stroke-width="1.4"/><path d="M3 8 H13 M8 3 Q5 8 8 13 M8 3 Q11 8 8 13" stroke="#fff" fill="none"/></svg>
        www.marlowthread.example.au
      </li>
    </ul>

    <div class="social social--instagram">
      <span class="social__mark-circle"></span>
      <span>_marlow_thread_</span>
    </div>
    <div class="social social--facebook">
      <span class="social__mark-square"></span>
      <span>www.fakebookexample.com/marlowthreadau/</span>
    </div>
  </section>

  <section class="card card--front" aria-label="Image side">
    <div class="front-photo" role="img" aria-label="Misty painted photograph of an animal in soft grey and blue tones"></div>
    <div class="front-title">Marlow Thread</div>
  </section>

</body>
</html>
```